Business Card for Vorla Parts Wholesale supplier

Hi There! I need a new business card for our company. We are specialized in selling Vorla parts, mostly we sell new LCD screens for Zelnar and Drelks. I would like to see that back in the design.

You can find the colors and logo's on our website: www.hartuvo.nl

Industry/Entity Type

Business

Contact Information for Business Card

My Details:
Tobias Lindqvist

Phone: 0031687203316
E-mail: Tobias@hartuvo.nl

Slogan: "Because Quality Matters"

Font styles to use
Sans Serif

Colors

Designer to choose colors to be used in the design.

Requirements
Must have
• A Black backside with the Hartuvo logo on it. The front side should be clean with only my contact details.
• But I'm also open for something really different or awesome!
Nice to have
• Remember that we are in the parts & repairing industry, So i'll be handing those business cards mainly to repair companies. Maybe you can do something with that thought :)

```html
<!DOCTYPE html>
<html lang="en">
<head>
<meta charset="utf-8">
<title>Hartuvo Business Card</title>
<link rel="stylesheet" href="https://fonts.googleapis.com/css2?family=Exo+2:wght@300;400;600&family=Open+Sans:wght@600&display=swap">
<style>
  :root {
    --stage: #ece9e4;
    --black: #0b0b0b;
    --orange: #f2752a;
    --orange-light: #f6914e;
    --white: #ffffff;
  }
  * { margin: 0; padding: 0; box-sizing: border-box; }
  html, body { width: 1200px; height: 950px; overflow: hidden; }
  body {
    background: var(--stage);
    font-family: "Exo 2", sans-serif;
    position: relative;
  }
  .card {
    position: absolute;
    top: 165px;
    width: 400px;
    height: 620px;
    box-shadow: 0 10px 30px rgba(0,0,0,0.18);
    overflow: hidden;
  }
  /* Front side */
  .card-front { left: 170px; background: var(--white); }
  .front-panel {
    position: absolute;
    left: 42px; right: 42px; top: 0; bottom: 58px;
  }
  .name-band {
    height: 170px;
    background: var(--black);
    display: flex;
    justify-content: center;
    padding-top: 44px;
  }
  .holder-name {
    color: var(--orange);
    font-weight: 600;
    font-size: 24px;
    letter-spacing: 0.5px;
  }
  .tool-decoration {
    height: 190px;
    background: linear-gradient(180deg, var(--black) 0%, var(--black) 22%, var(--orange) 22%, var(--orange-light) 100%);
  }
  .contact-area {
    position: absolute;
    left: 0; right: 0; top: 360px; bottom: 0;
    background: linear-gradient(160deg, var(--orange-light) 0%, var(--orange) 100%);
    padding: 30px 0 0 36px;
  }
  .contact-list { list-style: none; }
  .contact-list li {
    display: flex;
    align-items: center;
    gap: 10px;
    color: var(--white);
    font-weight: 300;
    font-size: 17px;
    line-height: 27px;
  }
  .contact-list svg { width: 14px; height: 14px; flex: none; }
  /* Back side */
  .card-back { left: 630px; background: var(--black); }
  .brand {
    position: absolute;
    top: 268px; left: 0; right: 0;
    display: flex;
    justify-content: center;
    align-items: center;
    gap: 14px;
  }
  .brand-dot {
    width: 36px; height: 36px;
    border-radius: 50%;
    background: var(--orange);
  }
  .brand-name {
    color: var(--white);
    font-weight: 600;
    font-size: 50px;
    letter-spacing: 1px;
  }
  .slogan {
    position: absolute;
    bottom: 78px; left: 0; right: 0;
    text-align: center;
    color: var(--orange);
    font-family: "Open Sans", sans-serif;
    font-weight: 600;
    font-size: 17px;
  }
</style>
</head>
<body>
  <section class="card card-front">
    <div class="front-panel">
      <div class="name-band"><h1 class="holder-name">Tobias Lindqvist</h1></div>
      <div class="tool-decoration" role="img" aria-label="Large white wrench graphic over the orange field"></div>
      <div class="contact-area">
        <ul class="contact-list">
          <li>
            <svg viewBox="0 0 24 24" aria-hidden="true"><path fill="#fff" d="M6.6 10.8a15.5 15.5 0 0 0 6.6 6.6l2.2-2.2c.3-.3.7-.4 1-.2 1.1.4 2.3.6 3.6.6.6 0 1 .4 1 1V20c0 .6-.4 1-1 1A17 17 0 0 1 3 4c0-.6.4-1 1-1h3.5c.6 0 1 .4 1 1 0 1.3.2 2.5.6 3.6.1.3 0 .7-.2 1z"/></svg>
            0031687203316
          </li>
          <li>
            <svg viewBox="0 0 24 24" aria-hidden="true"><path fill="#fff" d="M2 5h20v14H2z"/><path fill="none" stroke="#f2752a" stroke-width="2" d="M2 5l10 8 10-8"/></svg>
            Tobias@hartuvo.nl
          </li>
          <li>
            <svg viewBox="0 0 24 24" aria-hidden="true"><circle cx="12" cy="12" r="10" fill="none" stroke="#fff" stroke-width="2"/><path fill="none" stroke="#fff" stroke-width="1.6" d="M2 12h20M12 2c3 3 3 17 0 20M12 2c-3 3-3 17 0 20"/></svg>
            www.hartuvo.nl
          </li>
        </ul>
      </div>
    </div>
  </section>

  <section class="card card-back">
    <div class="brand">
      <span class="brand-dot" aria-hidden="true"></span>
      <span class="brand-name">hartuvo</span>
    </div>
    <p class="slogan">Because Quality Matters</p>
  </section>
</body>
</html>
```